Brightwell Practice Partners, Inc (www.brightwellpracticepartnrs.example) would like to design a website to convey a level of professionalism to healthcare providers that we are the place form them to visit for Contin. Education, Marketing and Management, Joint Venture Partnerships, etc.
We think we would like a WP Site so that we can use the dynamic and static sides of it's capabilities. We also want to have something that acts as a membership side where members can post their Bio and CV's and prospective employers can post help wanted ads.

Target Market(s)

Pediatricians, Pediatric Dentist, Employers seeking these doctors

Industry/Entity Type

Healthcare

Requirements
Must have
• Services:
Resumes/Bio
Help Wanted
Continuing Education Programs
Marketing & Management

```html
<!DOCTYPE html>
<html lang="en">
<head>
<meta charset="utf-8">
<title>BPP – Brightwell Practice Partners, Inc</title>
<link href="https://fonts.googleapis.com/css2?family=Roboto:wght@400;500&display=swap" rel="stylesheet">
<style>
:root{
  --brand:#7aa6d6;
  --brand-light:#a9c7e8;
  --brand-deep:#5f8fc4;
  --ink:#222;
  --heading:#1c4472;
  --link:#1f4f86;
  --panel:#f3f3f3;
  --rule:#d8d8d8;
  --white:#fff;
}
*{box-sizing:border-box;margin:0;padding:0}
html,body{width:947px;height:1200px;overflow:hidden}
body{position:relative;background:var(--white);font-family:"Roboto",Arial,sans-serif;color:var(--ink)}
.abs{position:absolute}
.site-header{left:0;top:0;width:947px;height:105px;background:var(--brand)}
.account-links{right:27px;top:9px;font-size:11px;color:var(--link)}
.account-links span{margin:0 5px}
.brand-name{left:42px;top:30px;font-size:26px;color:var(--white);font-weight:400;letter-spacing:.5px}
.main-nav{left:331px;top:47px;height:34px;display:flex}
.main-nav a{display:block;height:34px;line-height:34px;padding:0 18px;font-size:13px;color:var(--white);text-decoration:none;letter-spacing:.3px}
.main-nav a.current{background:var(--white);color:var(--brand-deep);padding:0 20px}
.hero{left:23px;top:81px;width:902px;height:263px;background:linear-gradient(90deg,#eef2f6 0%,#f6f6f6 40%,#eef3f7 70%,#f4f4f4 100%);border:2px solid var(--white)}
.promo{top:351px;height:148px;border:1px solid var(--brand-deep);background:linear-gradient(90deg,var(--brand) 0%,var(--brand-light) 50%,var(--brand) 100%);padding:17px 24px 0}
.promo h2{font-size:18px;font-weight:400;color:var(--heading);margin-bottom:4px}
.promo p{font-size:12.5px;line-height:16.7px;color:var(--heading)}
.promo .btn{position:absolute;bottom:10px;width:99px;height:29px;line-height:27px;text-align:center;font-size:12.5px;color:var(--ink);background:linear-gradient(#fff,#e6e6e6);border:1px solid #b9b9b9;border-radius:2px}
.promo.join{text-align:center}
.promo.join h2{text-align:left;padding-left:0}
.promo.join h2 b{font-weight:500}
.promo.join .free{font-size:31px;letter-spacing:2px;color:var(--heading);line-height:32px}
.promo.join p{font-size:11.5px}
.section-title{font-size:19px;font-weight:400;color:var(--heading)}
.opening{left:22px;width:596px;height:138px;background:var(--panel);padding:10px 11px 0;font-size:12.5px;line-height:16.6px}
.opening b{font-weight:500}
.opening .indent{padding-left:125px}
.opening .apply{position:absolute;left:12px;top:101px;width:93px;height:26px;line-height:24px;text-align:center;color:var(--heading);font-size:12.5px;background:linear-gradient(var(--brand-light),var(--brand));border:1px solid var(--brand-deep)}
.more{font-size:11px;color:var(--link)}
.side{left:634px;width:292px;font-size:12.2px;line-height:17.6px;text-align:justify;letter-spacing:.2px}
.rule{left:634px;top:729px;width:292px;height:1px;background:var(--rule)}
.site-footer{left:0;top:1153px;width:947px;height:47px;background:var(--brand);color:var(--white);font-size:10.5px}
.site-footer .legal{position:absolute;left:0;right:0;top:20px;text-align:center}
.site-footer .ver{position:absolute;right:22px;top:32px}
</style>
</head>
<body>
<header class="site-header abs">
  <div class="account-links abs">Sign up<span>|</span>Login</div>
  <div class="brand-name abs">BPP</div>
  <nav class="main-nav abs">
    <a class="current">Home</a><a>About us</a><a>View Profiles</a><a>Post&nbsp; profiles</a><a>Employers</a><a>Contact us</a>
  </nav>
</header>

<div class="hero abs" role="img" aria-label="Photo of four smiling doctors in white coats and scrubs with stethoscopes"></div>

<section class="promo abs" style="left:22px;width:296px">
  <h2>Post Profiles / CV’s</h2>
  <p>Lorem Ipsum is simply dummy text of the printing and typesetting industry. Lorem Ipsum has been the industry's standard dummy text</p>
  <div class="btn" style="right:26px">Post Profiles</div>
</section>
<section class="promo abs" style="left:327px;width:295px">
  <h2>Post Latest Openings</h2>
  <p>Lorem Ipsum is simply dummy text of the printing and typesetting industry. Lorem Ipsum has been the industry's standard dummy text</p>
  <div class="btn" style="right:21px">Post Ads</div>
</section>
<section class="promo join abs" style="left:630px;width:296px">
  <h2>Doctor’s <b>Join Now</b></h2>
  <div class="free">ITS FREE</div>
  <p>Lorem Ipsum is simply dummy text</p>
  <div class="btn" style="left:109px">Sign up</div>
</section>

<h2 class="section-title abs" style="left:22px;top:530px">Latest Openings</h2>

<article class="opening abs" style="top:563px">
  <div><b>Post</b> : Title</div>
  <div><b>Experience</b> :</div>
  <div><b>Post Requirements</b> : Lorem Ipsum is simply dummy text of the printing and typesetting industry.</div>
  <div class="indent">Lorem Ipsum has been the industry's standard</div>
  <div><b>Posted Date/Time</b> &nbsp;: 2 hours ago</div>
  <div class="apply">Apply Now</div>
</article>
<article class="opening abs" style="top:704px">
  <div><b>Post</b> : Title</div>
  <div><b>Experience</b> :</div>
  <div><b>Post Requirements</b> : Lorem Ipsum is simply dummy text of the printing and typesetting industry.</div>
  <div class="indent">Lorem Ipsum has been the industry's standard</div>
  <div><b>Posted Date/Time</b> &nbsp;: 2 hours ago</div>
  <div class="apply">Apply Now</div>
</article>
<article class="opening abs" style="top:845px">
  <div><b>Post</b> : Title</div>
  <div><b>Experience</b> :</div>
  <div><b>Post Requirements</b> : Lorem Ipsum is simply dummy text of the printing and typesetting industry.</div>
  <div class="indent">Lorem Ipsum has been the industry's standard</div>
  <div><b>Posted Date/Time</b> &nbsp;: 2 hours ago</div>
  <div class="apply">Apply Now</div>
</article>
<article class="opening abs" style="top:986px">
  <div><b>Post</b> : Title</div>
  <div><b>Experience</b> :</div>
  <div><b>Post Requirements</b> : Lorem Ipsum is simply dummy text of the printing and typesetting industry.</div>
  <div class="indent">Lorem Ipsum has been the industry's standard</div>
  <div><b>Posted Date/Time</b> &nbsp;: 2 hours ago</div>
  <div class="apply">Apply Now</div>
</article>
<div class="more abs" style="left:557px;top:1133px">View more</div>

<h2 class="section-title abs" style="left:634px;top:530px">About us</h2>
<p class="side abs" style="top:558px">Lorem Ipsum is simply dummy text of the printing and typesetting industry. Lorem Ipsum has been the industry's standard dummy text Lorem Ipsum is simply dummy text of the printing and typesetting industry. Lorem Ipsum has been the industry's standard dummy text Lorem Ipsum is simply dummy text of the printing and typesetting industry. Lorem Ipsum has been the industry's standard</p>
<div class="more abs" style="left:872px;top:704px">Read more</div>
<div class="rule abs"></div>

<h2 class="section-title abs" style="left:634px;top:745px">Testimonials</h2>
<p class="side abs" style="top:777px">Lorem Ipsum is simply dummy text of the printing and typesetting industry. Lorem Ipsum has been the industry's standard dummy text</p>
<p class="side abs" style="top:845px">Lorem Ipsum is simply dummy text of the printing and typesetting industry. Lorem Ipsum has been the industry's standard dummy text</p>
<p class="side abs" style="top:911px">Lorem Ipsum is simply dummy text of the printing and typesetting industry. Lorem Ipsum has been the industry's standard dummy text</p>
<div class="more abs" style="left:872px;top:971px">Read more</div>

<footer class="site-footer abs">
  <div class="legal">© 2012 BPP - Terms of Service - Privacy Policy - Program Policies</div>
  <div class="ver">V22</div>
</footer>
</body>
</html>
```